New Business Card Design Project

I need a design for business cards, i am an electrical business called "Corvane Electrical and Communications" i need the cards to be double sided with the company logo on the back (attached) the front needs to say my company name, web site, email address, telephone number, and ABN number and electrical license number. I am open to different arrangements of the information but would like the background to be incorporating something electrical or something that looks smart. open to all additional ideas also.

The company colours are orange and grey see logo attached.

Business Name: Corvane Electrical and Communications
Website: corvaneelectricalandcomms.example.com.au
Email: brent@corvaneelectricalandcomms.example.com.au
Telephone(mobile): 0481209736
ABN: 71208349162
Lic No: 418273D

Target Market(s)

Business entities, Project Managers, Accounts, Clients

Industry/Entity Type

Electrician

Contact Information for Business Card

I need a design for business cards, i am an electrical business called "Corvane Electrical and Communications" i need the cards to be double sided with the company logo on the back (attached) the front needs to say my company name

Font styles to use
Serif
Sans Serif

Colors
f37122
5c5c5c

Requirements
Must have
• Must have the Logo on the back open to different ways of it being on the back but had in mind to keep it central but again open to other options
Nice to have
• A real modern cool background that is eye catching yet contemporary
Should not have
• No backgrounds of a light bulb or plug or anything like that

```html
<!DOCTYPE html>
<html lang="en">
<head>
<meta charset="utf-8">
<title>Corvane Electrical and Communications – Business Card</title>
<link rel="stylesheet" href="https://fonts.googleapis.com/css2?family=Questrial&family=Montserrat:wght@600&display=swap">
<style>
  :root {
    --stage: #2b2b2d;
    --card-black: #050505;
    --card-grey: #5c5c5c;
    --orange: #f7a81b;
    --brand-orange: #f37122;
    --white: #ffffff;
  }
  html, body {
    margin: 0;
    padding: 0;
    width: 1200px;
    height: 900px;
    overflow: hidden;
    background: var(--stage);
    font-family: "Questrial", "Helvetica Neue", Arial, sans-serif;
  }
  .canvas {
    position: relative;
    width: 1200px;
    height: 900px;
  }
  .card {
    position: absolute;
    width: 640px;
    height: 390px;
    border-radius: 28px;
    overflow: hidden;
    background: var(--card-black);
    box-shadow: 0 14px 30px rgba(0,0,0,0.45);
  }
  .card--back { left: 110px; top: 45px; }
  .card--front { left: 450px; top: 470px; }

  .brand {
    position: absolute;
    display: flex;
    align-items: center;
    gap: 14px;
  }
  .brand__dot {
    width: 22px;
    height: 22px;
    border-radius: 50%;
    background: var(--orange);
    flex: none;
  }
  .brand__name {
    margin: 0;
    color: var(--white);
    font-family: "Montserrat", Arial, sans-serif;
    font-weight: 600;
    font-size: 30px;
    line-height: 1.15;
    letter-spacing: 0.5px;
  }
  .brand__name span { display: block; font-size: 17px; letter-spacing: 1.5px; }

  .card--back .brand { left: 150px; top: 140px; }
  .back__web {
    position: absolute;
    left: 186px;
    top: 240px;
    margin: 0;
    color: var(--white);
    font-size: 15px;
    letter-spacing: 0.3px;
  }

  .front__bg { position: absolute; inset: 0; }
  .card--front .brand { left: 48px; top: 128px; gap: 12px; }
  .card--front .brand__dot { width: 20px; height: 20px; }
  .card--front .brand__name { font-size: 26px; }
  .card--front .brand__name span { font-size: 12px; letter-spacing: 1px; margin-top: 2px; }
  .front__lic {
    position: absolute;
    left: 80px;
    top: 222px;
    margin: 0;
    font-size: 20px;
    color: var(--white);
  }
  .front__lic b { color: var(--orange); font-weight: 400; }

  .contact {
    position: absolute;
    right: 28px;
    top: 60px;
    width: 220px;
    text-align: right;
    color: var(--white);
  }
  .contact__name {
    margin: 0;
    color: var(--orange);
    font-size: 26px;
    letter-spacing: 0.5px;
  }
  .contact__role { margin: 2px 0 14px; font-size: 13px; letter-spacing: 1px; }
  .contact__line {
    margin: 4px 0;
    font-size: 14px;
    display: flex;
    justify-content: flex-end;
    align-items: center;
    gap: 8px;
  }
  .contact__line b { color: var(--orange); font-weight: 400; }
  .contact__line svg { width: 13px; height: 13px; flex: none; }
  .contact__links {
    position: absolute;
    right: 22px;
    bottom: 46px;
    text-align: right;
    color: var(--white);
    font-size: 11px;
    line-height: 1.4;
    margin: 0;
  }
</style>
</head>
<body>
<main class="canvas">

  <section class="card card--back" aria-label="Card back">
    <div class="brand">
      <span class="brand__dot"></span>
      <h1 class="brand__name">CORVANE<span>ELECTRICAL &amp; COMMUNICATIONS</span></h1>
    </div>
    <p class="back__web">www.corvaneelectricalandcomms.example.com.au</p>
  </section>

  <section class="card card--front" aria-label="Card front">
    <svg class="front__bg" viewBox="0 0 640 390" preserveAspectRatio="none" aria-hidden="true">
      <rect width="640" height="390" fill="var(--card-grey)"/>
      <path d="M0 0 H300 C410 70 410 260 250 390 H0 Z" fill="var(--card-black)"/>
      <path d="M300 0 C410 70 410 260 250 390" fill="none" stroke="var(--orange)" stroke-width="7"/>
    </svg>

    <div class="brand">
      <span class="brand__dot"></span>
      <h2 class="brand__name">CORVANE<span>ELECTRICAL &amp; COMMUNICATIONS</span></h2>
    </div>
    <p class="front__lic"><b>Lic No:</b> 418273D</p>

    <div class="contact">
      <p class="contact__name">MARLO KESTNER</p>
      <p class="contact__role">DIRECTOR</p>
      <p class="contact__line"><span><b>ABN:</b> 71208349162</span></p>
      <p class="contact__line"><span>0481 209-736</span>
        <svg viewBox="0 0 16 16" aria-hidden="true"><path d="M3 1h3l1.5 4-2 1.3a9 9 0 0 0 4.2 4.2L11 8.5l4 1.5v3a2 2 0 0 1-2 2A12 12 0 0 1 1 3a2 2 0 0 1 2-2z" fill="var(--orange)"/></svg>
      </p>
    </div>
    <p class="contact__links">brent@corvaneelectricalandcomms.example.com.au<br>www.corvaneelectricalandcomms.example.com.au</p>
  </section>

</main>
</body>
</html>
```